Tree Pruning Website

We need a website for a tree Arborist, pruning company called Maple Crest Canopy Works. We look after all types of trees, knock down trees and prune trees. Our target market is from domestic clients to government clients and everything in between.

We would like to see the use of our main colours which are orange and green

We are not looking forward in seeing a template that we have seen before but a unique template. We have designed 5 templates ourselves and we wish for the design community to take our designs to the next level.

We have also designed a template for things that **we are not** looking for (Version 4)

To make it fair for everyone, we are also not giving out any participation payments as we have had. One winner will take all of the payment!!!

I Have attached a image of the designs and a image of a tree.

We are just looking at the PSD file been developed. We have our own team who can slice the image up into a HTML format.

Target Market(s)

Everyone who needs to cut down a tree

Industry/Entity Type

Government

Requirements
Must have
• Logo on front page
A List of our services
jQuery slider on page
Phone Number on every page

```html
<!DOCTYPE html>
<html lang="en">
<head>
<meta charset="utf-8">
<title>Maple Crest Canopy Works</title>
<link href="https://fonts.googleapis.com/css2?family=Source+Sans+3:ital,wght@0,400;0,600;0,700;1,400&display=swap" rel="stylesheet">
<style>
:root{
  --green:#3b6d12;
  --green-bright:#5aa61a;
  --green-dark:#2f5b0c;
  --orange:#f7850b;
  --text:#555;
  --nav:#2b2b2b;
  --footer:#474747;
  --white:#fff;
}
*{margin:0;padding:0;box-sizing:border-box}
html,body{width:1157px;height:1200px;overflow:hidden}
body{position:relative;background:var(--white);font-family:"Source Sans 3",sans-serif;color:var(--text)}
.forest-band{position:absolute;left:0;top:0;width:1157px;height:499px;background:linear-gradient(90deg,#4f9a12,#6cbc26 30%,#5fae1c 60%,#4c9412)}
.site-header{position:absolute;left:125px;top:14px;width:906px;height:108px;background:linear-gradient(#f8f8f8,#e9e9e9)}
.brand{position:absolute;left:22px;top:30px;display:flex;align-items:center;gap:10px}
.brand-mark{width:42px;height:42px;border-radius:50%;background:var(--green-bright)}
.brand-name{font-size:30px;font-weight:700;color:var(--green);line-height:1;width:250px}
.call{position:absolute;right:20px;top:34px;display:flex;gap:10px;align-items:center}
.call-label{font-size:17px;color:#666;line-height:1}
.call-number{font-size:24px;color:var(--orange);font-weight:600;line-height:1.1}
.main-nav{position:absolute;left:125px;top:122px;width:906px;height:44px;background:linear-gradient(#454545,#1f1f1f);border-radius:8px 8px 0 0;display:flex;justify-content:space-between;align-items:center;padding:0 29px}
.main-nav a{color:#fff;text-decoration:none;font-size:14px;font-weight:600;letter-spacing:.5px}
.slider{position:absolute;left:125px;top:187px;width:906px;height:375px;background:#fff;padding:5px;box-shadow:0 1px 3px rgba(0,0,0,.25);display:flex}
.slide-photo{width:593px;height:365px;background:linear-gradient(160deg,#8fa0b8,#d8d4c6 45%,#6d7a4a)}
.slide-panel{flex:1;background:var(--green);padding:28px 22px;color:#fff;position:relative}
.slide-panel h2{font-weight:400;font-size:26px;line-height:1}
.slide-panel h2 span{display:block;font-size:40px;margin-top:2px}
.slide-panel p{font-size:13px;line-height:22px;margin-top:14px}
.btn{display:inline-block;margin-top:20px;background:var(--orange);color:#fff;font-weight:600;font-size:14px;padding:6px 18px;border-radius:16px;border:2px solid #ffb35c}
.dots{position:absolute;right:22px;bottom:18px;display:flex;gap:6px}
.dots i{width:13px;height:13px;border-radius:50%;background:#a3b68f}
.dots i:first-child{background:#fff}
.intro{position:absolute;left:125px;top:590px;width:663px}
.intro h3,.work h3{font-weight:400;font-size:25px;color:var(--green)}
.intro p{font-size:12.5px;line-height:19px;margin-top:8px;padding-bottom:20px;border-bottom:1px dashed #bbb}
.work{position:absolute;left:125px;top:730px}
.thumbs{display:flex;gap:20px;margin-top:10px}
.thumb{width:212px;height:107px;background:#fff;padding:4px;box-shadow:0 1px 3px rgba(0,0,0,.3)}
.thumb div{width:100%;height:100%}
.t1{background:linear-gradient(#6f8a4a,#1f3010)}
.t2{background:linear-gradient(#9ab04a,#6c8a2e 60%,#6a5a8e)}
.t3{background:linear-gradient(150deg,#8a98a8,#d9d2c2,#7a7a50)}
.services{position:absolute;left:819px;top:594px;width:212px;height:285px;background:#f4f4f4;border-radius:10px;box-shadow:0 1px 3px rgba(0,0,0,.2);overflow:hidden}
.services h3{background:linear-gradient(var(--green-bright),#3c7a10);color:#fff;font-weight:400;font-size:24px;padding:5px 17px;height:40px}
.services ul{list-style:none;padding:4px 16px 0}
.services li{font-size:12.5px;height:29px;line-height:29px;border-bottom:1px dashed #ccc;padding-left:22px;position:relative}
.services li:last-child{border:0}
.services li::before{content:"";position:absolute;left:3px;top:12px;width:6px;height:6px;border-radius:50%;background:var(--orange)}
.site-footer{position:absolute;left:0;top:906px;width:1157px;height:240px;background:var(--footer);color:#fff}
.site-footer h4{font-weight:400;font-size:22px}
.contact{position:absolute;left:125px;top:26px}
.contact .label{color:var(--orange);font-weight:600;font-size:15px;margin-top:4px}
.contact strong{font-size:13px;display:block;margin-top:2px}
.contact address{font-size:12px;line-height:20px}
.contact p{font-size:12px;line-height:20px;font-style:italic}
.contact p span{color:var(--orange)}
.contact .lines{margin-top:10px}
.map{position:absolute;left:317px;top:66px;width:212px;height:120px;background:linear-gradient(135deg,#e6e3da,#d9d6cc)}
.testimonial{position:absolute;left:588px;top:26px;width:260px}
.testimonial blockquote{font-size:12.5px;line-height:20px;font-style:italic;margin-top:12px;text-indent:32px;position:relative}
.testimonial .q{position:absolute;left:0;top:-6px;color:var(--green-bright);font-size:34px;font-style:normal;text-indent:0;font-weight:700}
.testimonial .by{text-align:right;font-size:12.5px;margin-top:8px;line-height:20px}
.testimonial .by span{display:block;color:var(--orange)}
.testimonial .all{display:block;margin-top:22px;font-size:12.5px;font-weight:600}
.connect{position:absolute;left:898px;top:26px}
.connect ul{list-style:none;margin-top:8px}
.connect li{font-size:13px;height:27px;display:flex;align-items:center;gap:9px}
.connect li i{width:15px;height:15px;border-radius:2px;background:#5a84c0}
.connect li:nth-child(4) i{background:#333;border:1px solid #777}
.connect li:nth-child(5) i{background:var(--orange)}
.legal{position:absolute;left:0;top:1146px;width:1157px;height:54px;background:var(--orange);color:#fff;font-size:12.5px;text-align:center;line-height:54px}
.legal span{color:#4a2a00}
</style>
</head>
<body>
<div class="forest-band" role="img" aria-label="Green forest backdrop"></div>

<header class="site-header">
  <div class="brand"><span class="brand-mark"></span><span class="brand-name">Maple Crest Canopy Works</span></div>
  <div class="call">
    <svg width="24" height="30" viewBox="0 0 24 30"><path d="M5 3l5 6-3 3c1 4 4 8 8 10l3-3 5 5-4 4C10 26 2 17 1 7z" fill="#c8261c"/></svg>
    <div><div class="call-label">Call Us:</div><div class="call-number">021 555 0142</div></div>
  </div>
</header>

<nav class="main-nav">
  <a href="#">HOME</a><a href="#">ABOUT US</a><a href="#">OUR SERVICES</a><a href="#">OUR WORK</a><a href="#">GET A QUOTE</a><a href="#">CONTACT US</a>
</nav>

<section class="slider">
  <div class="slide-photo" role="img" aria-label="Looking up into pale eucalyptus branches against the sky"></div>
  <div class="slide-panel">
    <h2>Welcome to <span>Tree Pruning</span></h2>
    <p>Aliquam molestie, mi et imperdiet euismod, dui purus auctor tellus, et interdum lacus lectus et ante. Sed accumsan sollicitudin sapien, sit amet adipiscing turpis gravida ac. In congue, neque ac lobortis volutpat, libero mauris varius mi, vitae suscipit ipsum ligula vitae risus.</p>
    <span class="btn">Learn More</span>
    <div class="dots"><i></i><i></i><i></i><i></i></div>
  </div>
</section>

<section class="intro">
  <h3>Why Maple Crest</h3>
  <p>Vestibulum ante ipsum primis in faucibus orci luctus et ultrices posuere cubilia Curae; Ut et scelerisque ante. Donec erat purus, faucibus vitae congue vel, porttitor nec lectus. Aenean a nibh eget turpis vehicula tempus ac sed massa. Vestibulum dolor nulla, ultrices ac tincidunt sed, laoreet non est. Suspendisse lobortis turpis in odio blandit ac interdum lorem euismod. Etiam risus massa, vulputate eu pellentesque et, consectetur a neque.</p>
</section>

<section class="work">
  <h3>Our Work</h3>
  <div class="thumbs">
    <div class="thumb"><div class="t1" role="img" aria-label="Sunlit forest with tall trunks"></div></div>
    <div class="thumb"><div class="t2" role="img" aria-label="Spring woodland with bluebells"></div></div>
    <div class="thumb"><div class="t3" role="img" aria-label="Pale eucalyptus branches from below"></div></div>
  </div>
</section>

<aside class="services">
  <h3>Our Services</h3>
  <ul>
    <li>Diagnosis</li><li>Treatment</li><li>Purning</li><li>Tree Removal</li><li>Stump Removel</li><li>Cabling &amp; Bracing</li><li>Arborist Consults</li><li>Tree Protection</li>
  </ul>
</aside>

<footer class="site-footer">
  <div class="contact">
    <h4>Contact Information</h4>
    <div class="label">Address:</div>
    <strong>MCCW</strong>
    <p>Maple Crest Canopy Works<br>48 Larchwood Road<br>BRAMLEY VALE, WA 6190</p>
    <p class="lines"><span>Tel:</span> 021 555 0142<br><span>Fax:</span> 021 555 0143<br><span>Email:</span> info@maplecrestcanopy.com</p>
  </div>
  <div class="map" role="img" aria-label="Street map showing the office location"></div>
  <div class="testimonial">
    <h4>What Other Says...</h4>
    <blockquote><span class="q">“</span>Vestibulum vel metus sit amet turpis bibendum tincidunt vel sit amet quam. Pellentesque habitant morbi tristique senectus et netus et malesuada fames ac turpis egestas.....</blockquote>
    <div class="by">By<span>Owen Hartley</span></div>
    <span class="all">READ ALL TESTIMONIALS</span>
  </div>
  <div class="connect">
    <h4>Connect Us</h4>
    <ul>
      <li><i></i>Friendspace</li><li><i></i>Chirper</li><li><i></i>WorkNet</li><li><i></i>Circlesphere</li><li><i></i>Rss Feed</li>
    </ul>
  </div>
</footer>

<div class="legal">© Copyright 2013. <span>MCCW</span> All Right Reserved</div>
</body>
</html>
```